U.S. Popcorn company needs business cards

We are a popcorn company that manufactures popcorn and sells it to grocery stores worldwide. Our theme is "Americana" and our logo is U.S. route 66 which is the most famous highway in the U.S.

We would like the design to be simple and to use both sides. On the back side we would like to see just the logo and website. The front would be normal details

Target Market(s)

Wholesalers, grocers and distributors

Industry/Entity Type

Manufacture

Contact Information for Business Card

Business name: Prairie Lantern Popcorn
Phone: +1 555 308 4726
Email: Dale@prairielanternpopcorn.com
website: www.prairielanternpopcorn.com
Tag Line: "Kernels worth the trip"
Name: Dale Whitcombe
Title: Founder/President

Requirements
Must have
• Either this design should be fun or clean and simple. I will let you show me your thougths.
Nice to have
• Anything that ties in the real Hwy Route 66.
• Colors might need to be red, white and blue incorporated.
Should not have
• Not be too busy.

```html
<!DOCTYPE html>
<html lang="en">
<head>
<meta charset="utf-8">
<title>Prairie Lantern Popcorn – Business Cards</title>
<link href="https://fonts.googleapis.com/css2?family=Mulish:ital,wght@0,400;0,700;0,800;1,400&display=swap" rel="stylesheet">
<style>
  :root {
    --navy: #112f64;
    --red: #d41a1f;
    --white: #ffffff;
    --card-white: #f7f7f7;
    --ink: #23365f;
    --backdrop: #e4e4e4;
  }
  * { margin: 0; padding: 0; box-sizing: border-box; }
  html, body { width: 1200px; height: 576px; overflow: hidden; }
  body {
    background: var(--backdrop);
    font-family: "Mulish", sans-serif;
    position: relative;
  }
  .card {
    position: absolute;
    border-radius: 6px;
    overflow: hidden;
  }
  .card--back {
    left: 82px; top: 139px; width: 484px; height: 291px;
    background: var(--navy);
  }
  .card--front {
    left: 603px; top: 138px; width: 479px; height: 292px;
    background: var(--card-white);
  }
  .brand {
    position: absolute;
    display: flex;
    flex-direction: column;
    align-items: center;
    justify-content: center;
    text-align: center;
    font-weight: 800;
    text-transform: uppercase;
    letter-spacing: 0.5px;
  }
  .brand__line { display: block; line-height: 1.05; }
  .card--back .brand {
    left: 148px; top: 52px; width: 188px; height: 170px;
    color: var(--white);
    font-size: 27px;
  }
  .card--front .brand {
    left: 245px; top: 38px; width: 212px; height: 198px;
    color: var(--navy);
    font-size: 29px;
  }
  .back-site {
    position: absolute;
    left: 0; right: 0; top: 254px;
    display: flex; align-items: center; justify-content: center;
    gap: 12px;
    color: var(--white);
    font-size: 12px;
    font-weight: 700;
    letter-spacing: 0.3px;
  }
  .back-site__rule {
    width: 42px; height: 2px;
    background: var(--red);
  }
  .person { position: absolute; left: 18px; top: 30px; }
  .person__name {
    color: var(--red);
    font-size: 16px;
    font-weight: 700;
  }
  .person__title {
    color: var(--ink);
    font-size: 11.5px;
    font-style: italic;
    margin-top: 1px;
  }
  .contacts {
    position: absolute; left: 20px; top: 216px;
    list-style: none;
    color: var(--ink);
    font-size: 12.5px;
  }
  .contacts__item {
    display: flex; align-items: center;
    height: 18px;
  }
  .contacts__icon { width: 11px; height: 11px; margin-right: 10px; flex: none; }
  .tagline {
    position: absolute;
    left: 245px; width: 212px; top: 251px;
    text-align: center;
    color: var(--ink);
    font-size: 14.5px;
    white-space: nowrap;
  }
  .tagline__lead { color: var(--red); font-weight: 700; }
</style>
</head>
<body>

<section class="card card--back" aria-label="Business card back">
  <div class="brand">
    <span class="brand__line">Prairie</span>
    <span class="brand__line">Lantern</span>
    <span class="brand__line">Popcorn</span>
  </div>
  <div class="back-site">
    <span class="back-site__rule"></span>
    <span>www.prairielanternpopcorn.com</span>
    <span class="back-site__rule"></span>
  </div>
</section>

<section class="card card--front" aria-label="Business card front">
  <div class="person">
    <p class="person__name">Dale Whitcombe</p>
    <p class="person__title">Founder/President</p>
  </div>

  <ul class="contacts">
    <li class="contacts__item">
      <svg class="contacts__icon" viewBox="0 0 12 12" aria-hidden="true">
        <path fill="#d41a1f" d="M1 4.2C1 2.6 3.2 1.5 6 1.5s5 1.1 5 2.7v.8H8.6V3.9H3.4V5H1zM3 6h6l1.5 3.5v1.5h-9V9.5z"/>
        <circle cx="6" cy="8.3" r="1.2" fill="#f7f7f7"/>
      </svg>
      <span>+1 555 308 4726</span>
    </li>
    <li class="contacts__item">
      <svg class="contacts__icon" viewBox="0 0 12 12" aria-hidden="true">
        <rect x="0.5" y="2.5" width="11" height="7.5" fill="#d41a1f"/>
        <path d="M0.8 2.8L6 7l5.2-4.2" fill="none" stroke="#f7f7f7" stroke-width="1"/>
      </svg>
      <span>Dale@prairielanternpopcorn.com</span>
    </li>
    <li class="contacts__item">
      <svg class="contacts__icon" viewBox="0 0 12 12" aria-hidden="true">
        <circle cx="6" cy="6" r="5.3" fill="#d41a1f"/>
        <g fill="none" stroke="#f7f7f7" stroke-width="0.8">
          <ellipse cx="6" cy="6" rx="2.2" ry="5.3"/>
          <path d="M0.7 6h10.6M1.5 3.5h9M1.5 8.5h9"/>
        </g>
      </svg>
      <span>www.prairielanternpopcorn.com</span>
    </li>
  </ul>

  <div class="brand">
    <span class="brand__line">Prairie</span>
    <span class="brand__line">Lantern</span>
    <span class="brand__line">Popcorn</span>
  </div>

  <p class="tagline">"<span class="tagline__lead">Kernels</span> worth the trip"</p>
</section>

</body>
</html>
```